Anzeigengestaltung für einen einen ambulanten Pflegedienst
Zielgruppe
Insgesamt möchte ich gern drei Anzeigen für das Internet gestalten haben. Ich betreibe einen ambulanten Pflegedienst. Die erste Anzeige soll dazu dienen Kunden anzusprechen, die einen Unterstützungsbedarf und / oder einen Beratungsbedarf haben. Die zweite Anzeige soll dazu dienen neues Personal anzuwerben. Die dritte Anzeige soll speziell potenzielle Azubis ansprechen. Die Anzeigen sind gedacht für Tralvio und Pexumora hauptsächlich. In den Druck sollte es schon 10cm x 8cm sein. Es wäre super wenn vielleicht auch eine Art Aufruf an ehrenamtliche Mitarbeiter erfolgt.
Aufgabenstellung
Die Anzeigen sollen den Stil der Homepage beibehalten. Freundlich, frisch und agil wirken. Alle sollten emotional ansprechend sein und gerade der für zukünftige Mitarbeiter sollte deutlich ein gutes Betriebsklima vermitteln. Als Datei habe ich einige Bilder, die bereits für die Homepage oder Flyer verwendet wurden hochgeladen. des Weiteren habe ich die einzelnen Seiten des Flyers hochgeladen.

```html
<!DOCTYPE html>
<html lang="de">
<head>
<meta charset="utf-8">
<title>Team Auvera – Ausbildung Pflege</title>
<link href="https://fonts.googleapis.com/css2?family=Playfair+Display:wght@400&family=Quicksand:wght@500;700&display=swap" rel="stylesheet">
<style>
  :root {
    --teal: #4aaea9;
    --green: #7aae3a;
    --ink: #5a5a5a;
    --paper: #ffffff;
    --band: #ecece7;
    --ring: #eeeee8;
  }
  html, body { margin: 0; padding: 0; overflow: hidden; }
  body { width: 1200px; height: 960px; background: var(--paper); }
  .ad {
    position: relative;
    width: 1200px; height: 960px;
    overflow: hidden;
    background: var(--paper);
    font-family: 'Quicksand', sans-serif;
  }
  .ad__band {
    position: absolute; left: 0; top: 810px;
    width: 1200px; height: 150px;
    background: var(--band);
  }
  .ad__photo { position: absolute; left: 0; top: 0; }
  .ad__kicker {
    position: absolute; left: 60px; top: 58px; margin: 0;
    font-family: 'Playfair Display', serif; font-weight: 400;
    font-size: 35px; color: var(--ink); line-height: 1;
  }
  .ad__headline {
    position: absolute; left: 58px; top: 120px; margin: 0;
    font-weight: 700; font-size: 66px; line-height: 74px; letter-spacing: 0.5px;
  }
  .ad__headline .line1 { display: block; color: var(--teal); }
  .ad__headline .line2 { display: block; color: var(--green); }
  .ad__rule {
    position: absolute; left: 60px; top: 288px;
    width: 454px; height: 6px; background: var(--green);
  }
  .pill {
    position: absolute; left: 48px; height: 62px;
    border-radius: 31px; color: #fff;
    font-family: 'Playfair Display', serif; font-size: 34px;
    line-height: 62px; padding-left: 27px; box-sizing: border-box;
    white-space: nowrap;
  }
  .pill--role { top: 341px; width: 470px; background: var(--teal); }
  .pill--apply { top: 855px; width: 686px; background: var(--green); }
  .benefits {
    position: absolute; left: 60px; top: 455px; margin: 0; padding: 0;
    list-style: none; color: var(--ink);
    font-weight: 500; font-size: 32px; line-height: 47px;
  }
  .benefits li { position: relative; padding-left: 30px; margin-bottom: 12px; }
  .benefits li::before {
    content: "+"; position: absolute; left: 0; top: -2px; color: var(--green);
  }
  .logo-badge {
    position: absolute; left: 625px; top: 42px;
    width: 244px; height: 244px; box-sizing: border-box;
    border-radius: 50%; background: var(--paper);
    border: 4px solid var(--ring);
    display: flex; flex-direction: column; align-items: center; justify-content: center;
  }
  .logo-badge__dot {
    width: 54px; height: 54px; border-radius: 50%;
    border: 5px solid var(--teal); box-sizing: border-box; margin-bottom: 18px;
  }
  .logo-badge__name {
    font-weight: 700; font-size: 26px; color: var(--ink); letter-spacing: 0.5px;
  }
  .ad__swoosh { position: absolute; left: 0; top: 0; pointer-events: none; }
</style>
</head>
<body>
<div class="ad">
  <div class="ad__band"></div>

  <svg class="ad__photo" width="1200" height="960" viewBox="0 0 1200 960">
    <defs>
      <linearGradient id="photoTone" x1="0" y1="0" x2="1" y2="1">
        <stop offset="0" stop-color="#cfe6e8"/>
        <stop offset="0.35" stop-color="#e7c9b4"/>
        <stop offset="0.6" stop-color="#2a9bbf"/>
        <stop offset="1" stop-color="#1f7f9d"/>
      </linearGradient>
    </defs>
    <circle cx="1115" cy="473" r="485" fill="url(#photoTone)" role="img"
      aria-label="Foto: lächelnde Auszubildende in blauer Pflegekleidung mit Stift im Unterricht, im Hintergrund weitere Auszubildende"/>
  </svg>

  <p class="ad__kicker">Junge Talente gesucht!</p>
  <h1 class="ad__headline">
    <span class="line1">Komm in unser</span>
    <span class="line2">Team Auvera</span>
  </h1>
  <div class="ad__rule"></div>

  <div class="pill pill--role">Auszubildende:r Pfleger:in</div>

  <ul class="benefits">
    <li>Ausbildung mit persöhnlichem<br>Ansprechpartnern</li>
    <li>Praxiseinsätze gemeinsam<br>mit der Praxisleitung</li>
    <li>genügend Ruhephasen<br>im Dienstplan</li>
  </ul>

  <svg class="ad__swoosh" width="1200" height="960" viewBox="0 0 1200 960" aria-hidden="true">
    <path d="M591 665 C591 610 625 582 690 577 C718 575 735 580 749 589" fill="none" stroke="var(--teal)" stroke-width="6" stroke-linecap="round"/>
    <path d="M619 725 C620 680 632 632 660 619 C695 612 740 620 767 631" fill="none" stroke="var(--green)" stroke-width="6" stroke-linecap="round"/>
  </svg>

  <div class="logo-badge">
    <div class="logo-badge__dot"></div>
    <div class="logo-badge__name">TEAM AUVERA</div>
  </div>

  <div class="pill pill--apply">Bewirb dich auf: www.team-auvera.de</div>
</div>
</body>
</html>
```